Site for entrepreneurs/small businesses needs Logo, Homepage

Looking for a logo, either an icon, or stylized text, or a combination of both, and a home page design which fits with it. The logo will be for use on the public website as well as for printed collateral (business cards, post cards, brochures and various other marketing materials).

The site is called Orbitwell (Orbitwell.example). This is to be a national, and eventually an international brand. The new service will provide an easy-to-use platform for entrepreneurs to build their business and web presence together in an integrated way which allows them to focus on their core competency.

The site/service will be dead-simple to use, A/B/C, 1/2/3. We will want some sort of "Get started for FREE" promotional space to collect the person's email address with multiple points of interest which guide the user back to this one call to action: sign up for free. We will feature editorial/blog stories, customer testimonials, and present several key features the the reader just can't live without if they are starting a new business.

Criteria:
* Refer to our comparable sites/logos in the design document attached
* Incorporate our color scheme (but complementary colors welcome)
* No Serif fonts!
* No photo-realistic elements for logo
* Logo must present well in gray scale and/or black/white (for printed materials)
* Strokes/borders that are wider to promote simplicity (vs. thin/precise lines which promote technical complexity)

Inspirations:
* Creative/Custom (but legible) fonts
* Excitement, energetic, jumping for joy
* Karate / Ninja / Power / Precision
* Dance Moves
* Regional influences: California, Silicon Valley, West Coast, Surf City, Beaches, Sunset
* Simple/easy, no-brainer solutions

Target Market(s)

Small Businesses / Entrepreneurs

Logo Text

Orbitwell or Orbitwell.example

Number of Pages Required

1 page

Font styles to use
Sans Serif
Decorative

Requirements
Must have
• See the attached style guide (PDF)

```html
<!DOCTYPE html>
<html lang="en">
<head>
<meta charset="utf-8">
<title>Orbitwell – Build your business</title>
<link rel="stylesheet" href="https://fonts.googleapis.com/css2?family=Montserrat:wght@400;600;700;800&family=Open+Sans:wght@400;600&display=swap">
<style>
:root{
  --hero:#123d4b;
  --hero-deep:#0d3140;
  --navy:#0b2452;
  --orange:#f7941d;
  --ink:#1d1d1f;
  --muted:#6d6d72;
  --paper:#ffffff;
  --mist:#f1f1f3;
  --line:#d9d9de;
  --sky:#2a8bc9;
  --teal:#1e9bb0;
}
*{box-sizing:border-box;margin:0;padding:0}
html,body{width:1200px;height:4192px;overflow:hidden}
body{position:relative;background:var(--paper);font-family:"Open Sans",Arial,sans-serif;color:var(--ink)}
.section{position:absolute;left:0;width:1200px}
.btn{display:inline-block;background:var(--orange);color:#fff;font-family:"Montserrat",Arial,sans-serif;font-weight:700;font-size:13px;letter-spacing:.5px;border-radius:20px;padding:11px 26px;text-transform:uppercase}
.btn-small{font-size:10px;padding:6px 14px;border-radius:12px}
.art{position:absolute}
.section-title{position:absolute;left:0;right:0;font-family:"Montserrat",Arial,sans-serif;font-weight:800;font-size:30px;text-align:center;text-transform:uppercase;color:var(--ink)}
.title-rule{position:absolute;left:565px;width:70px;height:3px;background:var(--line)}

/* brand */
.brand-mark{display:flex;align-items:center;gap:10px;font-family:"Montserrat",Arial,sans-serif;font-weight:700;color:#fff}
.brand-dot{border-radius:50%;background:var(--orange);flex:none}

/* hero */
.hero{top:0;height:680px;background:linear-gradient(180deg,var(--hero) 0%,var(--hero-deep) 100%)}
.hero .brand-mark{position:absolute;left:40px;top:24px;font-size:32px}
.hero .brand-dot{width:16px;height:16px}
.nav{position:absolute;right:40px;top:26px;display:flex;gap:6px}
.nav a{font-family:"Montserrat",Arial,sans-serif;font-weight:700;font-size:12px;color:#fff;text-decoration:none;padding:6px 12px}
.nav a.active{background:var(--orange);border-radius:3px}
.hero-title{position:absolute;left:132px;top:188px;font-family:"Montserrat",Arial,sans-serif;font-weight:800;font-size:40px;line-height:1.15;color:#fff}
.signup{position:absolute;left:132px;top:312px;width:272px}
.signup .field{display:flex;align-items:center;gap:10px;background:#fff;border-radius:4px;height:34px;padding:0 12px;margin-bottom:14px;font-size:12px;color:#444}
.signup .btn{width:100%;text-align:center;margin-top:12px;border-radius:4px}
.hero-art{left:600px;top:60px;width:540px;height:580px;border-radius:28px;background:linear-gradient(150deg,#f2c53d 0%,#e8543f 45%,#2fa79a 100%)}

/* welcome */
.welcome{top:680px;height:660px;background:var(--paper)}
.welcome-art{left:50px;top:100px;width:470px;height:440px;border-radius:28px;background:linear-gradient(160deg,#d9dcf3 0%,#8b82dc 55%,#f3c53f 100%)}
.welcome-copy{position:absolute;left:732px;top:110px;width:300px}
.kicker{font-family:"Montserrat",Arial,sans-serif;font-weight:800;font-size:16px;text-transform:uppercase}
.welcome-copy .brand-mark{color:var(--navy);font-size:48px;margin:10px 0 20px}
.welcome-copy .brand-dot{width:22px;height:22px}
.body-text{font-size:13px;line-height:1.6;color:var(--muted)}
.welcome-copy .btn{margin-top:32px}

/* services */
.services{top:1340px;height:500px;background:var(--mist)}
.services .section-title{top:64px}
.services .title-rule{top:116px}
.service-grid{position:absolute;left:132px;top:164px;display:flex;gap:32px}
.service-card{width:208px;height:270px;background:#fff;border-radius:4px;box-shadow:0 6px 16px rgba(0,0,0,.12);text-align:center;padding:36px 18px 0}
.service-card svg{display:block;margin:0 auto 14px}
.service-card h3{font-family:"Montserrat",Arial,sans-serif;font-weight:700;font-size:15px;margin-bottom:12px}
.service-card p{font-size:11px;line-height:1.5;color:var(--muted);margin-bottom:18px;height:34px}

/* features */
.features{top:1840px;height:680px;background:var(--paper)}
.features-slant{position:absolute;left:0;top:0}
.features-copy{position:absolute;left:148px;top:80px;width:340px}
.features-copy h2{font-family:"Montserrat",Arial,sans-serif;font-weight:800;font-size:30px;margin-bottom:18px}
.feature-list{list-style:none;margin:24px 0 34px}
.feature-list li{display:flex;align-items:center;gap:10px;font-size:12px;color:#333;margin-bottom:9px}
.feature-list li::before{content:"";width:7px;height:7px;border-radius:50%;background:var(--orange);flex:none}
.features-art{left:530px;top:50px;width:620px;height:480px;border-radius:50%;background:linear-gradient(160deg,#9fd0f0 0%,#4aa3dc 55%,#e45a6a 100%)}

/* blog */
.blog{top:2520px;height:600px;background:var(--mist)}
.blog .section-title{top:0}
.blog .title-rule{top:52px}
.blog-grid{position:absolute;left:148px;top:120px;display:flex;gap:56px}
.blog-card{width:252px;height:420px;background:#fff;box-shadow:0 6px 16px rgba(0,0,0,.12)}
.blog-thumb{height:206px}
.blog-body{padding:20px 22px}
.blog-body h3{font-family:"Montserrat",Arial,sans-serif;font-weight:800;font-size:14px;line-height:1.35;text-transform:uppercase;margin-bottom:12px}
.blog-body p{font-size:11px;line-height:1.5;color:var(--muted);margin-bottom:16px}

/* testimonials */
.testimonials{top:3120px;height:696px;background:var(--paper)}
.testimonials .section-title{top:70px}
.testimonials .title-rule{top:122px}
.quote-card{position:absolute;background:#fff;box-shadow:0 6px 18px rgba(0,0,0,.13);text-align:center;padding:58px 26px 0}
.avatar{position:absolute;left:50%;top:-32px;width:64px;height:64px;margin-left:-32px;border-radius:50%;background:linear-gradient(180deg,#c9956c,#7a4e32);border:3px solid #fff}
.quote-card h4{font-family:"Montserrat",Arial,sans-serif;font-weight:700;font-size:10px;letter-spacing:.5px}
.stars{color:var(--orange);font-size:11px;letter-spacing:2px;margin:4px 0 12px}
.quote-card p{font-size:11px;line-height:1.6;color:var(--muted)}
.slider-arrow{position:absolute;width:30px;height:30px;border-radius:50%;background:var(--orange);display:flex;align-items:center;justify-content:center}

/* footer */
.footer{top:3816px;height:376px;background:var(--navy);color:#fff}
.footer .brand-mark{position:absolute;left:150px;top:146px;font-size:42px}
.footer .brand-dot{width:20px;height:20px}
.footer-col{position:absolute;top:62px}
.footer-col h5{font-family:"Montserrat",Arial,sans-serif;font-weight:700;font-size:11px;text-transform:uppercase;margin-bottom:16px}
.footer-col li{list-style:none;font-size:11px;color:#c7cfdf;margin-bottom:8px;display:flex;align-items:flex-start;gap:8px;line-height:1.45}
.social-dot{width:20px;height:20px;border-radius:50%;background:var(--sky);flex:none}
.footer-col.connect li{align-items:center;margin-bottom:14px}
.copyright{position:absolute;left:0;right:0;top:336px;text-align:center;font-size:10px;color:#aab4c8}
</style>
</head>
<body>

<header class="section hero">
  <div class="brand-mark"><span class="brand-dot"></span>Orbitwell</div>
  <nav class="nav">
    <a class="active">HOME</a><a>ABOUT US</a><a>SERVICES</a><a>BLOG</a><a>CONTACT US</a>
  </nav>
  <h1 class="hero-title">GET STARTED<br>FOR FREE</h1>
  <form class="signup">
    <div class="field">
      <svg width="14" height="10" viewBox="0 0 14 10"><rect x="1" y="1" width="12" height="8" fill="none" stroke="#666" stroke-width="1.4"/><path d="M1 1l6 5 6-5" fill="none" stroke="#666" stroke-width="1.4"/></svg>
      E-mail Id
    </div>
    <div class="field">
      <svg width="12" height="12" viewBox="0 0 12 12"><circle cx="6" cy="4" r="3" fill="#666"/><path d="M0 12a6 5 0 0 1 12 0z" fill="#666"/></svg>
      Name
    </div>
    <span class="btn">SIGN UP FOR FREE</span>
  </form>
  <div class="art hero-art" role="img" aria-label="Isometric illustration of a team building a business on puzzle-piece platforms"></div>
</header>

<section class="section welcome">
  <div class="art welcome-art" role="img" aria-label="Isometric illustration of a digital workspace with screens and charts"></div>
  <div class="welcome-copy">
    <div class="kicker">WELCOME TO</div>
    <div class="brand-mark"><span class="brand-dot"></span>Orbitwell</div>
    <p class="body-text">We help new founders set up a brand, a website and daily tools in one calm place, so every hour goes into the work they love most and the customers they serve.</p>
    <span class="btn">READ MORE</span>
  </div>
</section>

<section class="section services">
  <h2 class="section-title">OUR SERVICES</h2>
  <div class="title-rule"></div>
  <div class="service-grid">
    <div class="service-card">
      <svg width="40" height="40" viewBox="0 0 40 40"><circle cx="20" cy="11" r="8" fill="#14304f"/><path d="M5 40c0-11 6-18 15-18s15 7 15 18z" fill="#14304f"/></svg>
      <h3>Entrepreneurs</h3>
      <p>Simple tools that help you plan, launch and grow your idea.</p>
      <span class="btn btn-small">READ MORE</span>
    </div>
    <div class="service-card">
      <svg width="48" height="40" viewBox="0 0 48 40"><path d="M2 14l10-4 12 10-6 6z" fill="#14304f"/><path d="M46 14l-10-4-14 8 10 12z" fill="#14304f"/><path d="M14 24l6 6 4-2 4 4 6-6" fill="none" stroke="#14304f" stroke-width="4" stroke-linejoin="round"/></svg>
      <h3>Build Business</h3>
      <p>Set up payments, forms and pages without writing any code.</p>
      <span class="btn btn-small">READ MORE</span>
    </div>
    <div class="service-card">
      <svg width="40" height="40" viewBox="0 0 40 40"><rect x="4" y="4" width="14" height="14" fill="#14304f"/><rect x="22" y="4" width="14" height="14" fill="#14304f"/><rect x="4" y="22" width="14" height="14" fill="#14304f"/><circle cx="29" cy="29" r="7" fill="#14304f"/></svg>
      <h3>Easy to Use</h3>
      <p>Clear steps guide you from first idea to a live business.</p>
      <span class="btn btn-small">READ MORE</span>
    </div>
    <div class="service-card">
      <svg width="40" height="40" viewBox="0 0 40 40"><path d="M6 22a14 14 0 0 1 28 0" fill="none" stroke="#14304f" stroke-width="4"/><rect x="3" y="20" width="8" height="12" rx="3" fill="#14304f"/><rect x="29" y="20" width="8" height="12" rx="3" fill="#14304f"/><path d="M33 32c0 4-4 6-10 6" fill="none" stroke="#14304f" stroke-width="3"/></svg>
      <h3>Support</h3>
      <p>Friendly experts answer questions whenever you need help.</p>
      <span class="btn btn-small">READ MORE</span>
    </div>
  </div>
</section>

<section class="section features">
  <svg class="features-slant" width="1200" height="680" viewBox="0 0 1200 680"><polygon points="0,680 1200,440 1200,680" fill="#f1f1f3"/></svg>
  <div class="features-copy">
    <h2>FEATURES</h2>
    <p class="body-text">Everything a new business needs, bundled into one clear and friendly workspace.</p>
    <ul class="feature-list">
      <li>Launch a site in a single afternoon</li>
      <li>Collect leads with ready-made forms</li>
      <li>Send invoices straight from your dashboard</li>
      <li>Track visitors with simple clear reports</li>
      <li>Book clients with a shared calendar</li>
      <li>Get help from real people any time</li>
    </ul>
    <span class="btn">READ MORE</span>
  </div>
  <div class="art features-art" role="img" aria-label="Isometric illustration of people working around connected screens on a round platform"></div>
</section>

<section class="section blog">
  <h2 class="section-title">LATEST BLOG</h2>
  <div class="title-rule"></div>
  <div class="blog-grid">
    <article class="blog-card">
      <div class="blog-thumb" role="img" aria-label="Illustration of people planning around a network of ideas" style="background:linear-gradient(180deg,#1e9bb0,#137a8e)"></div>
      <div class="blog-body">
        <h3>Lorem ipsum dolor sit sectetur adipisci</h3>
        <p>Practical steps for turning a side project into a steady small business.</p>
        <span class="btn btn-small">READ MORE</span>
      </div>
    </article>
    <article class="blog-card">
      <div class="blog-thumb" role="img" aria-label="Illustration of people climbing a stack of books" style="background:linear-gradient(180deg,#2b7fc0,#1f6fa8)"></div>
      <div class="blog-body">
        <h3>Lorem ipsum dolor sit sectetur adipisci</h3>
        <p>Simple habits that keep your books tidy and your cash flow healthy.</p>
        <span class="btn btn-small">READ MORE</span>
      </div>
    </article>
    <article class="blog-card">
      <div class="blog-thumb" role="img" aria-label="Illustration of a team running up a hill toward a flag" style="background:linear-gradient(180deg,#3aa0dc,#cfe7f5)"></div>
      <div class="blog-body">
        <h3>Lorem ipsum dolor sit sectetur adipisci</h3>
        <p>How small teams set clear goals and celebrate every early win together.</p>
        <span class="btn btn-small">READ MORE</span>
      </div>
    </article>
  </div>
</section>

<section class="section testimonials">
  <h2 class="section-title">TESTIMONIALS</h2>
  <div class="title-rule"></div>
  <div class="slider-arrow" style="left:136px;top:330px"><svg width="10" height="10" viewBox="0 0 10 10"><path d="M7 1L3 5l4 4" fill="none" stroke="#fff" stroke-width="2"/></svg></div>
  <div class="quote-card" style="left:252px;top:222px;width:250px;height:246px">
    <div class="avatar" role="img" aria-label="Customer portrait"></div>
    <h4>DANA REYES</h4>
    <div class="stars">★★★★★</div>
    <p>Orbitwell made it easy to launch my shop. I set up my site, my mailing list and my bookings in one weekend without any help.</p>
  </div>
  <div class="quote-card" style="left:636px;top:320px;width:304px;height:262px">
    <div class="avatar" role="img" aria-label="Customer portrait" style="background:linear-gradient(180deg,#e3b07e,#8a5a3a)"></div>
    <h4>DANA REYES</h4>
    <div class="stars">★★★★★</div>
    <p>Orbitwell gave my studio one home for everything. Clients find me, book a time and pay online, and I can finally focus on design.</p>
  </div>
  <div class="slider-arrow" style="left:1034px;top:440px"><svg width="10" height="10" viewBox="0 0 10 10"><path d="M3 1l4 4-4 4" fill="none" stroke="#fff" stroke-width="2"/></svg></div>
</section>

<footer class="section footer">
  <div class="brand-mark"><span class="brand-dot"></span>Orbitwell</div>
  <div class="footer-col" style="left:480px">
    <h5>CONTACT US</h5>
    <ul>
      <li><svg width="10" height="13" viewBox="0 0 10 13"><path d="M5 0a5 5 0 0 1 5 5c0 4-5 8-5 8S0 9 0 5a5 5 0 0 1 5-5z" fill="#fff"/><circle cx="5" cy="5" r="2" fill="#0b2452"/></svg><span>123 Harbor Avenue,<br>Seaside, CA 90000</span></li>
      <li><svg width="11" height="11" viewBox="0 0 11 11"><path d="M2 0l2 3-1 1.5a7 7 0 0 0 3.5 3.5L8 7l3 2-1 2C5 11 0 6 0 1z" fill="#fff"/></svg><span>(555) 010-2048</span></li>
      <li><svg width="12" height="9" viewBox="0 0 12 9"><rect x=".7" y=".7" width="10.6" height="7.6" fill="none" stroke="#fff" stroke-width="1.4"/><path d="M1 1l5 4 5-4" fill="none" stroke="#fff" stroke-width="1.4"/></svg><span>hello@orbitwell.example</span></li>
    </ul>
  </div>
  <div class="footer-col" style="left:736px">
    <h5>MENU</h5>
    <ul><li>Home</li><li>About Us</li><li>Services</li><li>Blog</li><li>Contact Us</li></ul>
  </div>
  <div class="footer-col connect" style="left:940px">
    <h5>CONNECT WITH US</h5>
    <ul>
      <li><span class="social-dot"></span>Friendlane</li>
      <li><span class="social-dot"></span>Chirpline</li>
      <li><span class="social-dot"></span>Worknet</li>
    </ul>
  </div>
  <div class="copyright">Copyright © 2018 All Rights Reserved</div>
</footer>

</body>
</html>
```